TalkHarbor - Language Coaching Services

Sleek, innovative, trendy design for Language Coaching business.

TalkHarbor is a new UK based company that provides Language Coaching services. We offer highly personalized on-line and face to face language courses. We also impart learning techniques workshops based on the latest neuroscience research for second-language acquisition.

Target Market(s)

See attached info

Industry/Entity Type

Consulting

Contact Information for Business Card

TalkHarbor
DaniaKV@talkharbor.co.uk
TalkHarbor.co.uk
London, UK

Font styles to use
Sans Serif

```html
<!DOCTYPE html>
<html lang="en">
<head>
<meta charset="utf-8">
<title>TalkHarbor – Business Card</title>
<link rel="stylesheet" href="https://fonts.googleapis.com/css2?family=Roboto:wght@300;400;500;700&display=swap">
<style>
  :root {
    --stage: #e9ecef;
    --blue-light: #1a9ad6;
    --blue-deep: #0b5d8f;
    --brand-blue: #1b86c4;
    --name-blue: #17679d;
    --ink-grey: #6d7276;
    --text-dark: #4a4f53;
    --white: #ffffff;
  }
  * { box-sizing: border-box; margin: 0; padding: 0; }
  html, body {
    width: 1200px; height: 960px; overflow: hidden;
    background: var(--stage);
    font-family: "Roboto", Arial, sans-serif;
  }
  .canvas { position: relative; width: 1200px; height: 960px; }
  .card {
    position: absolute; left: 240px; width: 720px; height: 411px;
    box-shadow: 0 10px 28px rgba(0,0,0,.18);
    overflow: hidden;
  }
  /* Back face */
  .card-back {
    top: 50px;
    background: radial-gradient(ellipse at 48% 45%, var(--blue-light) 0%, #1183bf 40%, var(--blue-deep) 100%);
    color: var(--white);
  }
  .back-mark {
    position: absolute; left: 50%; top: 50%;
    transform: translate(-50%, -58%);
    display: flex; flex-direction: column; align-items: center; gap: 16px;
  }
  .back-mark .ring {
    width: 130px; height: 130px; border-radius: 50%;
    border: 9px solid var(--white);
  }
  .back-mark .brand-name {
    font-size: 30px; font-weight: 400; letter-spacing: 3px;
  }
  .back-url {
    position: absolute; right: 44px; bottom: 36px;
    font-size: 15px; font-weight: 300; letter-spacing: 4px;
  }
  /* Front face */
  .card-front { top: 509px; background: var(--white); }
  .front-brand {
    position: absolute; right: 40px; top: 24px;
    display: flex; flex-direction: column; align-items: center; gap: 10px;
  }
  .front-brand .ring {
    width: 84px; height: 84px; border-radius: 50%;
    border: 6px solid var(--brand-blue);
  }
  .front-brand .brand-name {
    font-size: 36px; font-weight: 500; letter-spacing: 1px;
    color: var(--brand-blue); text-transform: uppercase;
  }
  .divider-arrow { position: absolute; left: 36px; top: 178px; }
  .website {
    position: absolute; right: 44px; top: 200px;
    font-size: 15px; color: var(--text-dark);
  }
  .person { position: absolute; left: 40px; top: 214px; }
  .person .name {
    font-size: 23px; font-weight: 700; color: var(--name-blue); letter-spacing: .5px;
    line-height: 1.1;
  }
  .person .role {
    margin-top: 6px;
    font-size: 16px; font-weight: 500; color: var(--ink-grey);
  }
  .person .rule {
    margin-top: 10px; width: 210px; height: 2px; background: var(--brand-blue);
  }
  .contacts { list-style: none; margin-top: 16px; }
  .contacts li {
    display: flex; align-items: center; gap: 12px;
    font-size: 17px; color: var(--text-dark); margin-bottom: 9px;
  }
  .contacts svg { flex: none; }
</style>
</head>
<body>
<main class="canvas">

  <section class="card card-back" aria-label="Card back">
    <div class="back-mark">
      <div class="ring"></div>
      <span class="brand-name">TalkHarbor</span>
    </div>
    <span class="back-url">talkharbor.co.uk</span>
  </section>

  <section class="card card-front" aria-label="Card front">
    <div class="front-brand">
      <div class="ring"></div>
      <span class="brand-name">TalkHarbor</span>
    </div>

    <svg class="divider-arrow" width="650" height="14" viewBox="0 0 650 14" aria-hidden="true">
      <line x1="0" y1="7" x2="638" y2="7" stroke="var(--brand-blue)" stroke-width="2"/>
      <polygon points="636,1 650,7 636,13" fill="var(--brand-blue)"/>
    </svg>

    <span class="website">www.talkharbor.co.uk</span>

    <div class="person">
      <p class="name">ELLIS HARTLEY</p>
      <p class="role">CEO/FOUNDER</p>
      <div class="rule"></div>
      <ul class="contacts">
        <li>
          <svg width="14" height="20" viewBox="0 0 14 20" aria-label="Phone">
            <rect x="1" y="1" width="12" height="18" rx="2" fill="none" stroke="var(--name-blue)" stroke-width="2"/>
            <rect x="5" y="15" width="4" height="1.6" fill="var(--name-blue)"/>
          </svg>
          020 7946 0183
        </li>
        <li>
          <svg width="16" height="12" viewBox="0 0 16 12" aria-label="Email">
            <rect x="0" y="0" width="16" height="12" fill="var(--name-blue)"/>
            <polyline points="0.5,0.5 8,7 15.5,0.5" fill="none" stroke="var(--white)" stroke-width="1.4"/>
          </svg>
          info@talkharbor.co.uk
        </li>
      </ul>
    </div>
  </section>

</main>
</body>
</html>
```